New web design for a service provider in the medical field

We are looking for a new design for our website. We are a company that repairs and sells medical endoscopes. Our customers include doctors and hospitals. Our current website can be found at https://lumavex.de/en/lumavex-english.
We need a new web design (without programming) for the following 3 pages:
-Startpage https://lumavex.de/en/lumavex-english/
-Used endoscopes https://lumavex.de/en/used-endoscopes/
-Purchase https://lumavex.de/en/purchase/
The design should be modern and stylish.
The blue color of the logo should be reflected on the page, but not too intrusive.
I have uploaded the images from the header. If more images are needed, let me know and I will upload them.

Target Market(s)
Doctors and hospitals

```html
<!DOCTYPE html>
<html lang="en">
<head>
<meta charset="utf-8">
<title>Lumavex – Sell Your Endoscope</title>
<link href="https://fonts.googleapis.com/css2?family=Barlow:wght@500;600;700&family=Roboto:wght@400;500&display=swap" rel="stylesheet">
<style>
:root{
  --blue:#0a74bb;
  --accent:#27a6de;
  --ink:#333333;
  --muted:#555b61;
  --line:#0a74bb;
  --navy:#064476;
  --navy-deep:#022e52;
  --white:#ffffff;
  --rule:#eef0f2;
}
*{box-sizing:border-box;margin:0;padding:0}
html,body{width:1200px;height:2257px;overflow:hidden;background:var(--white)}
body{position:relative;font-family:"Roboto",sans-serif;color:var(--ink)}
.abs{position:absolute}
svg{display:block}
.heading{font-family:"Barlow",sans-serif;font-weight:700;color:var(--ink)}
.accent{color:var(--accent)}

/* top bar */
.topbar{left:0;top:0;width:1200px;height:38px;border-bottom:1px solid var(--rule);font-size:11px;color:var(--muted)}
.topbar .item{position:absolute;top:13px;display:flex;align-items:center;gap:7px}
.topbar .dot{width:10px;height:10px;border-radius:50%;border:1px solid var(--muted)}
/* nav */
.brand{left:128px;top:60px;font-family:"Roboto",sans-serif;font-weight:500;font-size:19px;color:var(--blue);display:flex;align-items:center;gap:8px}
.brand .mark{width:14px;height:14px;border-radius:50%;background:var(--accent)}
.nav{left:330px;top:67px;display:flex;gap:26px;font-size:12px;color:var(--ink)}
.btn{display:flex;align-items:center;justify-content:center;border-radius:20px;background:var(--blue);color:var(--white);font-weight:500;font-size:12px}
.hero{left:0;top:111px;width:1200px;height:329px;background:linear-gradient(90deg,#ececee 0%,#e9e8ec 45%,#d9d8de 70%,#bfbec6 100%)}
.hero h1{position:absolute;left:155px;top:104px;font-size:38px}
.hero p{position:absolute;left:156px;top:160px;width:430px;font-size:11.3px;line-height:21px;color:var(--muted)}

/* form */
.eyebrow{left:0;width:1200px;text-align:center;top:500px;font-size:15px;color:var(--muted)}
.title{left:0;width:1200px;text-align:center;top:530px;font-size:36px}
.group{font-family:"Barlow",sans-serif;font-weight:600;font-size:15px;color:var(--ink);left:268px}
.label{font-weight:500;font-size:12.5px;color:var(--ink)}
.field{width:312px;height:43px;border:1px solid var(--line);border-radius:22px;display:flex;align-items:center;justify-content:space-between;padding:0 17px 0 18px;font-size:11.5px;color:var(--muted)}
.col1{left:268px}.col2{left:618px}
.textarea{left:268px;top:1236px;width:662px;height:147px;border:1px solid var(--line);border-radius:16px;padding:16px 13px 0 18px;font-size:11.5px;color:var(--muted);display:flex;justify-content:space-between;align-items:flex-start}
.upload{left:268px;top:1425px;width:127px;height:127px;border:1px solid var(--line);border-radius:8px;display:flex;align-items:center;justify-content:center}
.check{left:268px;top:1586px;width:18px;height:18px;border:1px solid var(--line);border-radius:4px}
.consent{left:300px;top:1581px;width:600px;font-size:9.7px;line-height:21px;color:var(--muted)}

/* cta + footer */
.footer{left:0;top:1883px;width:1200px;height:324px;background:var(--navy)}
.cta{left:128px;top:1820px;width:943px;height:132px;border-radius:10px;background:var(--blue);color:var(--white)}
.cta .kicker{position:absolute;left:35px;top:36px;font-size:15px}
.cta h2{position:absolute;left:34px;top:56px;font-family:"Barlow",sans-serif;font-weight:700;font-size:35px}
.cta .btn-light{position:absolute;left:753px;top:59px;width:156px;height:37px;border-radius:20px;background:var(--white);color:var(--ink);font-size:11.5px;font-weight:500;display:flex;align-items:center;justify-content:center}
.f-brand{left:165px;top:2015px;font-weight:500;font-size:17px;color:var(--white);display:flex;align-items:center;gap:8px}
.f-brand .mark{width:12px;height:12px;border-radius:50%;background:var(--accent)}
.f-contact{left:158px;font-size:10px;color:var(--white);display:flex;align-items:center;gap:7px}
.socials{left:156px;top:2144px;display:flex;gap:25px}
.socials span{width:10px;height:10px;border-radius:50%;border:1.2px solid var(--white)}
.f-col h3{font-family:"Barlow",sans-serif;font-weight:600;font-size:14px;color:var(--white);margin-bottom:14px}
.f-col ul{list-style:none;font-size:10px;color:var(--white);line-height:24.5px}
.f-news p{font-size:10px;line-height:19px;color:var(--white);width:225px}
.subscribe{left:820px;top:2110px;width:223px;height:32px;border-radius:17px;background:var(--white);border:1.5px solid var(--accent);font-size:8.5px;color:var(--muted);padding-left:16px;display:flex;align-items:center}
.subscribe .go{position:absolute;right:2px;top:1px;width:27px;height:27px;border-radius:50%;background:var(--blue);display:flex;align-items:center;justify-content:center}
.legal{left:0;top:2207px;width:1200px;height:50px;background:var(--navy-deep);font-size:10px;color:var(--white)}
.legal span{position:absolute;top:20px}
</style>
</head>
<body>

<header>
  <div class="abs topbar">
    <div class="item" style="left:128px">
      <svg width="12" height="10" viewBox="0 0 12 10"><rect x="0.5" y="0.5" width="11" height="9" fill="none" stroke="#8a9096"/><path d="M1 1l5 4 5-4" fill="none" stroke="#8a9096"/></svg>
      info@lumavex.de
    </div>
    <div class="item" style="left:274px">
      <svg width="11" height="11" viewBox="0 0 24 24"><path d="M5 3h4l2 5-3 2a12 12 0 0 0 6 6l2-3 5 2v4a2 2 0 0 1-2 2A18 18 0 0 1 3 5a2 2 0 0 1 2-2z" fill="none" stroke="#8a9096" stroke-width="2"/></svg>
      +49 4100 555 012-0
    </div>
    <div class="item" style="left:636px">Pick Up Order</div>
    <div class="item" style="left:729px">About US</div>
    <div class="item" style="left:803px">Contact Us</div>
    <div class="item" style="left:900px"><svg width="17" height="11" viewBox="0 0 17 11"><rect width="17" height="11" fill="#1f3f8a"/><path d="M0 0l17 11M17 0L0 11" stroke="#fff" stroke-width="2"/><path d="M8.5 0v11M0 5.5h17" stroke="#fff" stroke-width="3"/><path d="M8.5 0v11M0 5.5h17" stroke="#c8202f" stroke-width="1.5"/></svg>
      <svg width="8" height="8" viewBox="0 0 8 8"><path d="M1 3l3 3 3-3" fill="none" stroke="#8a9096"/></svg></div>
    <div class="item" style="left:979px"><span class="dot"></span></div>
    <div class="item" style="left:1005px"><span class="dot"></span></div>
    <div class="item" style="left:1033px"><span class="dot"></span></div>
    <div class="item" style="left:1062px"><span class="dot"></span></div>
  </div>

  <div class="abs brand"><span class="mark"></span>Lumavex</div>
  <nav class="abs nav">
    <span>Home</span><span>Endoscope Repair</span><span>Used Endoscopes</span><span>Endoscopy Systems</span><span>Endoscopy Accessories</span>
  </nav>
  <a class="abs btn" style="left:941px;top:57px;width:130px;height:34px">Purchase Now!</a>
</header>

<section class="abs hero" role="img" aria-label="Close-up photograph of endoscope control handles on a light background">
  <h1 class="heading">Do You Want to Sell <span class="accent">Your Endoscope?</span></h1>
  <p>We are always interested in buying used endoscopes, accessories and peripherals from Olvaris, Pentrix and Fujora at fair conditions. We can promise you an objective offer with a clear conscience! Use the form below… <span style="color:var(--ink);font-weight:500">READ MORE</span></p>
</section>

<main>
  <div class="abs eyebrow">Lorum Ipsum Dolor</div>
  <h2 class="abs title heading">Sed Perspiciatis <span class="accent">Unde Omnis</span></h2>

  <h3 class="abs group" style="top:618px">Personal Informations</h3>
  <div class="abs label col1" style="top:660px">Salutation</div>
  <div class="abs label col2" style="top:660px">co. / dr. off.</div>
  <div class="abs field col1" style="top:684px">Select salutation<svg width="11" height="7" viewBox="0 0 11 7"><path d="M1 1l4.5 4.5L10 1" fill="none" stroke="#0a74bb" stroke-width="1.8"/></svg></div>
  <div class="abs field col2" style="top:684px">Company / doctors office<svg width="11" height="7" viewBox="0 0 11 7"><path d="M1 1l4.5 4.5L10 1" fill="none" stroke="#0a74bb" stroke-width="1.8"/></svg></div>

  <div class="abs label col1" style="top:742px">Surname</div>
  <div class="abs label col2" style="top:742px">First Name</div>
  <div class="abs field col1" style="top:766px">Enter surname<svg width="12" height="13" viewBox="0 0 12 13"><circle cx="6" cy="3.3" r="3" fill="#0a74bb"/><path d="M0 13c0-4 2.5-6 6-6s6 2 6 6z" fill="#0a74bb"/></svg></div>
  <div class="abs field col2" style="top:766px">Enter first name<svg width="12" height="13" viewBox="0 0 12 13"><circle cx="6" cy="3.3" r="3" fill="#0a74bb"/><path d="M0 13c0-4 2.5-6 6-6s6 2 6 6z" fill="#0a74bb"/></svg></div>

  <div class="abs label col1" style="top:824px">Email Address</div>
  <div class="abs label col2" style="top:824px">Contact Number</div>
  <div class="abs field col1" style="top:848px">Enter email<svg width="13" height="10" viewBox="0 0 13 10"><rect x="0.8" y="0.8" width="11.4" height="8.4" rx="1" fill="none" stroke="#0a74bb" stroke-width="1.4"/><path d="M1 1.5l5.5 4 5.5-4" fill="none" stroke="#0a74bb" stroke-width="1.4"/></svg></div>
  <div class="abs field col2" style="top:848px">Enter phone number<svg width="13" height="13" viewBox="0 0 24 24"><path d="M5 3h4l2 5-3 2a12 12 0 0 0 6 6l2-3 5 2v4a2 2 0 0 1-2 2A18 18 0 0 1 3 5a2 2 0 0 1 2-2z" fill="none" stroke="#0a74bb" stroke-width="2"/></svg></div>

  <h3 class="abs group" style="top:935px">Informations About The Device</h3>
  <div class="abs label col1" style="top:977px">Brand</div>
  <div class="abs label col2" style="top:977px">Model</div>
  <div class="abs field col1" style="top:1001px">Select brand<svg width="11" height="7" viewBox="0 0 11 7"><path d="M1 1l4.5 4.5L10 1" fill="none" stroke="#0a74bb" stroke-width="1.8"/></svg></div>
  <div class="abs field col2" style="top:1001px">Select model<svg width="11" height="7" viewBox="0 0 11 7"><path d="M1 1l4.5 4.5L10 1" fill="none" stroke="#0a74bb" stroke-width="1.8"/></svg></div>

  <div class="abs label col1" style="top:1059px">Defects / Damage</div>
  <div class="abs label col2" style="top:1059px">Asking Price</div>
  <div class="abs field col1" style="top:1083px">Write here<svg width="13" height="13" viewBox="0 0 24 24"><path d="M11 4H4v16h16v-7" fill="none" stroke="#0a74bb" stroke-width="2.2"/><path d="M18 2l4 4-10 10H8v-4z" fill="none" stroke="#0a74bb" stroke-width="2.2"/></svg></div>
  <div class="abs field col2" style="top:1083px">Enter here<svg width="13" height="13" viewBox="0 0 24 24"><path d="M13 2h9v9L11 22 2 13z" fill="#0a74bb"/><circle cx="17" cy="7" r="2" fill="#fff"/></svg></div>

  <h3 class="abs group" style="top:1170px">Remarks &amp; Picture</h3>
  <div class="abs label col1" style="top:1212px">Remark</div>
  <div class="abs textarea">Type here<svg width="13" height="13" viewBox="0 0 24 24"><path d="M11 4H4v16h16v-7" fill="none" stroke="#0a74bb" stroke-width="2.2"/><path d="M18 2l4 4-10 10H8v-4z" fill="none" stroke="#0a74bb" stroke-width="2.2"/></svg></div>

  <div class="abs label col1" style="top:1401px">Upload Images</div>
  <div class="abs upload"><svg width="55" height="45" viewBox="0 0 55 45"><path d="M3 10h12l4-7h17l4 7h12v32H3z" fill="none" stroke="#0a74bb" stroke-width="2.4" stroke-linejoin="round"/><circle cx="27.5" cy="25" r="9" fill="none" stroke="#0a74bb" stroke-width="2.4"/></svg></div>

  <div class="abs check"></div>
  <p class="abs consent">I have read the privacy policy and accept it. I agree above input will be transmitted to Lumavex GmbH to get in contact with me respectively to process my request and store all needed informations. Neither a transfer to third parties will happen, nor a use for advertising purposes by Lumavex GmbH!</p>

  <a class="abs btn" style="left:268px;top:1683px;width:144px;height:37px">Send Now</a>
</main>

<footer>
  <div class="abs footer"></div>
  <div class="abs cta">
    <div class="kicker">Get In Touch</div>
    <h2>How Can We Help You?</h2>
    <a class="btn-light">Contact Us Now</a>
  </div>

  <div class="abs f-brand"><span class="mark"></span>Lumavex</div>
  <div class="abs f-contact" style="top:2088px"><svg width="10" height="10" viewBox="0 0 24 24"><path d="M5 3h4l2 5-3 2a12 12 0 0 0 6 6l2-3 5 2v4a2 2 0 0 1-2 2A18 18 0 0 1 3 5a2 2 0 0 1 2-2z" fill="#fff"/></svg>+49 4100 555 012-0</div>
  <div class="abs f-contact" style="top:2112px"><svg width="10" height="8" viewBox="0 0 10 8"><rect width="10" height="8" fill="#fff"/><path d="M0 0.5l5 3.5 5-3.5" fill="none" stroke="#064476"/></svg>info@lumavex.de</div>
  <div class="abs socials"><span></span><span></span><span></span><span></span></div>

  <div class="abs f-col" style="left:430px;top:2011px">
    <h3>Quick Links</h3>
    <ul><li>Home</li><li>Endoscope Repair</li><li>Used Endoscopes</li><li>Endoscopy Systems</li><li>Endoscopy Accessories</li></ul>
  </div>
  <div class="abs f-col" style="left:661px;top:2011px">
    <h3>Usefull Links</h3>
    <ul><li>Information</li><li>About Us</li><li>Contact Us</li><li>TOS</li><li>FAQ</li></ul>
  </div>
  <div class="abs f-col f-news" style="left:820px;top:2011px">
    <h3>Newsletter</h3>
    <p>Lorem ipsum dolor sit consectetur adipiscing elit sed do eiusmod tempor incididunt ut labore et dolore magna aliqua.</p>
  </div>
  <div class="abs subscribe">Your Email
    <span class="go"><svg width="12" height="12" viewBox="0 0 24 24"><path d="M22 2L2 10l8 3 3 8z M10 13L22 2" fill="none" stroke="#fff" stroke-width="2" stroke-linejoin="round"/></svg></span>
  </div>

  <div class="abs legal">
    <span style="left:156px">2022 All rights reserved</span>
    <span style="left:856px">Privacy Policy</span>
    <span style="left:955px">Terms &amp; Conditions</span>
  </div>
</footer>

</body>
</html>
```